Business Card Design Project

I need a business card design for an Organic drive thru coffee kiosk. We will serve organic coffee, teas & smoothies and will serve healthy breakfast food/snacks for people on the go.
I want the card to have 2-3 colors max (earthy colors like browns, greens and so on).
I have attached the logo I want used and would love to play off the theme of "balance."
Include:
Sun-Leaf Coffee
address: 3712 Pelwin Ct. Raleigh, NC 27699
phone: 919-555-0143
website: www.sun-leaf.com (website is not up yet but still include it on card)
email: Dorothy@sun-leaf.com
I want one of the following sayings somewhere on the card (the front or back is fine):
"Eat & Drink Well, on the run!"
"Break the fast with Sun-Leaf"
Maybe on the back list what we offer:
-Organic coffee, espresso & tea
-Blendora smoothies & protein shakes
-Zippy Tonic (100% fresh local fruit and veggies)
-Vital Nibbles
College age to 55
Business

```html
<!DOCTYPE html>
<html lang="en">
<head>
<meta charset="utf-8">
<title>Sun-Leaf Coffee – Business Card</title>
<link rel="stylesheet" href="https://fonts.googleapis.com/css2?family=Cabin:wght@400;500;600&display=swap">
<style>
  :root {
    --page-bg: #e7e4df;
    --card-front: #efeeec;
    --card-back: #4a2b21;
    --brand-brown: #4a2b21;
    --rust: #7d3826;
    --rust-dark: #5e2f22;
    --leaf-green: #8cbf2e;
    --text-dark: #3a2a24;
  }
  * { box-sizing: border-box; margin: 0; padding: 0; }
  html, body {
    width: 1200px; height: 900px; overflow: hidden;
    background: var(--page-bg);
    font-family: "Cabin", sans-serif;
  }
  .sheet {
    position: relative; width: 1200px; height: 900px;
    display: flex; align-items: center; justify-content: center; gap: 40px;
  }
  .card {
    position: relative; width: 540px; height: 309px; overflow: hidden;
    box-shadow: 0 6px 18px rgba(0,0,0,.18);
  }

  /* Front */
  .card--front { background: var(--card-front); color: var(--text-dark); }
  .brand {
    position: absolute; left: 44px; top: 38px;
    display: flex; align-items: center; gap: 10px;
  }
  .brand__name {
    font-size: 38px; font-weight: 600; color: var(--brand-brown);
    line-height: 1; letter-spacing: -0.5px;
  }
  .brand__mark {
    width: 30px; height: 30px; border-radius: 50%; background: var(--rust);
  }
  .brand__tagline {
    position: absolute; left: 46px; top: 84px;
    font-size: 9px; letter-spacing: 2.2px; color: var(--rust);
    text-transform: uppercase;
  }
  .website {
    position: absolute; left: 46px; top: 138px;
    font-size: 13px; color: var(--text-dark);
  }
  .contact {
    position: absolute; left: 272px; top: 176px;
    font-size: 13px; line-height: 1.35; color: var(--text-dark);
  }
  .contact__name {
    font-size: 19px; font-variant: small-caps; letter-spacing: .5px;
    line-height: 1.1; color: var(--brand-brown);
  }
  .contact__title { margin-bottom: 6px; }
  .contact__row { display: flex; gap: 8px; }
  .contact__label { font-weight: 600; width: 10px; }

  /* Back */
  .card--back { background: var(--card-back); }
  .back-decor { position: absolute; left: 0; top: 0; }
  .offer {
    position: absolute; left: 230px; top: 62px; width: 280px;
    color: var(--leaf-green); font-size: 12.5px; line-height: 1.35;
  }
  .offer__slogan {
    font-size: 12.5px; text-transform: uppercase; letter-spacing: .4px;
    padding-bottom: 6px; border-bottom: 1px solid var(--leaf-green);
    margin-bottom: 10px; text-align: right;
  }
  .offer__list { list-style: none; }
  .offer__list li { position: relative; padding-left: 12px; }
  .offer__list li::before {
    content: "•"; position: absolute; left: 0; top: 0;
  }
</style>
</head>
<body>
<main class="sheet">
  <section class="card card--front" aria-label="Business card front">
    <div class="brand">
      <span class="brand__name">Sun-Leaf</span>
      <span class="brand__mark"></span>
    </div>
    <div class="brand__tagline">Organic Coffee + Cafe</div>
    <div class="website">www.sun-leaf.com</div>
    <div class="contact">
      <div class="contact__name">Dorothy Reyes</div>
      <div class="contact__title">Operation Manager</div>
      <div class="contact__row"><span class="contact__label">T</span><span>919-555-0143</span></div>
      <div class="contact__row"><span class="contact__label">E</span><span>dorothy@sun-leaf.com</span></div>
      <div>3712 Pelwin Ct. Raleigh, NC 27699</div>
    </div>
  </section>

  <section class="card card--back" aria-label="Business card back">
    <svg class="back-decor" width="220" height="170" viewBox="0 0 220 170" aria-hidden="true">
      <circle cx="85" cy="40" r="125" fill="var(--rust-dark)"/>
      <circle cx="85" cy="40" r="108" fill="var(--rust)"/>
    </svg>
    <div class="offer">
      <div class="offer__slogan">Eat &amp; Drink Well, on the run!</div>
      <ul class="offer__list">
        <li>Organic coffee, espresso &amp; tea</li>
        <li>Blendora smoothies &amp; protein shakes</li>
        <li>Zippy Tonic (100% fresh local fruit and veggies)</li>
        <li>Vital Nibbles</li>
      </ul>
    </div>
  </section>
</main>
</body>
</html>
```